FinTech company looking to revamp and expand client-facing interface for our financial models

Pellworth Engines currently has a very simple website that allows clients to interact with our financial models. We are looking to completely redesign the current site and add several extra pages to provide extra functionality. We want the design to have a modern, slick feel, that will work on both a desktop or a tablet. It should be straightforward for clients to move between different pages at any time, and clear from the layout how to interact with the more advanced features. We have included screenshots of existing pages in the attached design brief, as well as sketches of the functionality required by the new pages, but can't provide a direct link to the current site.
Target Market(s)
Professional investors that will be paying to access the interface
Industry/Entity Type
Finance
Number of Pages Required
4 page
Colors
Designer to choose colors to be used in the design.
Look and feel
Each slider illustrates characteristics of the customer's brand and the style your logo design should communicate.

```html
<!DOCTYPE html>
<html lang="en">
<head>
<meta charset="utf-8">
<title>Korva · Backtest</title>
<link href="https://fonts.googleapis.com/css2?family=Open+Sans:wght@400;600;700&family=Roboto:wght@400&display=swap" rel="stylesheet">
<style>
:root{
  --page:#ececec;
  --white:#ffffff;
  --ink:#111111;
  --navy:#003366;
  --teal:#00695f;
  --dim:#3d3d3d;
  --dim-card:#444444;
  --dim-head:#2a2a2a;
  --dim-text:#5e5e5e;
  --line:#dddddd;
  --modal:#f0f0f0;
  --scroll:#e2e2e2;
}
*{box-sizing:border-box;margin:0;padding:0}
html,body{width:1200px;height:1122px;overflow:hidden;background:var(--page)}
body{font-family:"Open Sans",Arial,sans-serif;color:var(--ink)}
.stage{position:absolute;left:0;top:0;width:1300px;height:1215px;transform:scale(0.9231);transform-origin:0 0}
.abs{position:absolute}
.frame{left:15px;top:15px;width:1270px;height:1185px;background:var(--dim)}
.topbar{left:15px;top:15px;width:1270px;height:60px;background:var(--white)}
.nav-cell{position:absolute;top:0;height:60px;display:flex;align-items:center;justify-content:center;gap:8px;font-weight:700;font-size:14px;border-left:1px solid #e6e6e6}
.brand{font-size:18px;border-left:none}
.nav-cell.active{background:var(--navy);color:var(--white)}
.dimmed{color:var(--dim-text);font-family:Roboto,Arial,sans-serif;font-size:17px}
.card{background:var(--dim-card);border-radius:4px}
.thead{background:var(--dim-head);display:flex;align-items:center}
.thead span{flex:1;text-align:center;color:#555;font-size:17px}
.row{position:absolute;display:flex;align-items:center}
.modal{left:15px;top:115px;width:785px;height:620px;background:var(--modal);border-radius:0 4px 4px 0}
.tab{display:flex;align-items:center;justify-content:center;font-weight:700;font-size:14px}
.panel{background:var(--white);border:1px solid var(--line);border-radius:4px}
.field{background:var(--white);border:1px solid #cfcfcf;border-radius:3px;box-shadow:inset 0 1px 2px rgba(0,0,0,.12);font-size:16px;display:flex;align-items:center;padding-left:12px}
.btn{display:flex;align-items:center;justify-content:center;color:var(--white);font-weight:700;border-radius:3px}
.model-item{position:absolute;left:0;width:330px;height:49px;border-bottom:1px solid #ececec;display:flex;align-items:center;padding-left:20px;font-weight:700;font-size:17px}
.model-item.selected{background:var(--teal);color:var(--white)}
.param{position:absolute;left:0;width:368px;height:50px;border-bottom:1px solid #ececec}
.param label{position:absolute;left:17px;top:13px;font-weight:700;font-size:17px}
.param .field{position:absolute;left:113px;top:9px;width:242px;height:31px}
.options{left:800px;top:330px;width:50px;height:250px;background:var(--white);border-radius:0 4px 4px 0}
</style>
</head>
<body>
<div class="stage">
  <div class="abs frame"></div>

  <header class="abs topbar">
    <div class="nav-cell brand" style="left:0;width:180px">KORVA</div>
    <div class="nav-cell" style="left:180px;width:90px">250D</div>
    <div class="nav-cell" style="left:270px;width:90px">83D</div>
    <div class="nav-cell" style="left:360px;width:90px;border-right:1px solid #e6e6e6">42D</div>
    <div class="nav-cell" style="left:585px;width:141px">
      <svg width="26" height="24" viewBox="0 0 26 24"><path d="M13 2 2 12h3v10h6v-6h4v6h6V12h3z" fill="none" stroke="#111" stroke-width="2.4" stroke-linejoin="round"/></svg>MODELS</div>
    <div class="nav-cell" style="left:726px;width:177px">
      <svg width="26" height="26" viewBox="0 0 26 26"><g fill="#111"><circle cx="13" cy="13" r="3"/><circle cx="13" cy="4" r="2"/><circle cx="13" cy="22" r="2"/><circle cx="4" cy="13" r="2"/><circle cx="22" cy="13" r="2"/><circle cx="6.5" cy="6.5" r="2"/><circle cx="19.5" cy="19.5" r="2"/><circle cx="19.5" cy="6.5" r="2"/><circle cx="6.5" cy="19.5" r="2"/></g></svg>SENSITIVITIES</div>
    <div class="nav-cell" style="left:903px;width:160px">
      <svg width="24" height="24" viewBox="0 0 24 24"><g fill="none" stroke="#111" stroke-width="1.8"><circle cx="6" cy="6" r="4"/><circle cx="18" cy="6" r="4"/><circle cx="6" cy="18" r="4"/><circle cx="18" cy="18" r="4"/></g></svg>PORTFOLIO</div>
    <div class="nav-cell active" style="left:1063px;width:152px">
      <svg width="26" height="22" viewBox="0 0 26 22"><rect x="1.5" y="1.5" width="23" height="19" fill="none" stroke="#fff" stroke-width="2"/><path d="M5 16l5-6 4 4 6-8" fill="none" stroke="#fff" stroke-width="2"/></svg>BACKTEST</div>
  </header>

  <!-- background content behind the open panel -->
  <div class="abs card" style="left:790px;top:115px;width:475px;height:425px"></div>
  <svg class="abs" style="left:790px;top:250px" width="475" height="240" viewBox="0 0 475 240">
    <line x1="10" y1="14" x2="275" y2="14" stroke="#2c4a66" stroke-width="5"/>
    <line x1="10" y1="200" x2="320" y2="200" stroke="#555" stroke-width="1"/>
    <g fill="#555"><circle cx="360" cy="11" r="3"/><circle cx="360" cy="30" r="3" fill="#6b5a3a"/><circle cx="360" cy="49" r="3" fill="#3f5a30"/><circle cx="360" cy="68" r="3"/><circle cx="360" cy="87" r="3"/><circle cx="360" cy="106" r="3"/><circle cx="360" cy="125" r="3"/><circle cx="360" cy="143" r="3"/><circle cx="360" cy="161" r="3" fill="#3f5a30"/><circle cx="360" cy="180" r="3"/><circle cx="360" cy="198" r="3" fill="#333"/></g>
    <text x="377" y="15" font-size="11" fill="#555" font-family="serif">Names</text>
    <text x="100" y="226" font-size="11" fill="#555">May 2019</text>
    <text x="245" y="226" font-size="11" fill="#555">Jul 2019</text>
  </svg>
  <div class="abs" style="left:1175px;top:592px;display:flex;align-items:center;gap:6px;color:#555;font-weight:700;font-size:17px">
    <svg width="26" height="24" viewBox="0 0 26 24"><path d="M10 5H3v17h17v-7M13 14 24 3m-7 0h7v7" fill="none" stroke="#555" stroke-width="2"/></svg>Export</div>
  <div class="abs card" style="left:105px;top:700px;width:400px;height:420px"></div>
  <div class="abs card" style="left:545px;top:700px;width:720px;height:420px"></div>
  <div class="abs thead" style="left:790px;top:630px;width:475px;height:70px"><span>Close</span><span>Size</span><span>Return</span></div>
  <div class="abs dimmed" style="left:175px;top:727px;line-height:69px;width:240px">
    <div style="display:flex;justify-content:space-between"><span>Stat 1</span><span>0.5</span></div>
    <div style="display:flex;justify-content:space-between"><span>Stat 2</span><span>-3</span></div>
    <div style="display:flex;justify-content:space-between"><span>Stat 3</span><span>30%</span></div>
    <div style="display:flex;justify-content:space-between"><span>Stat 4</span><span>0.5</span></div>
    <div style="display:flex;justify-content:space-between"><span>Stat 5</span><span>-3</span></div>
    <div style="display:flex;justify-content:space-between"><span>Stat 6</span><span>30%</span></div>
  </div>
  <div class="abs dimmed" style="left:594px;top:727px;line-height:69px;width:580px">
    <div style="display:flex"><span style="width:180px">2018-04-05</span><span style="width:205px">2018-04-07</span><span style="width:160px">13</span><span>5%</span></div>
    <div style="display:flex"><span style="width:180px">2018-04-05</span><span style="width:205px">2018-04-07</span><span style="width:160px">12</span><span>7%</span></div>
    <div style="display:flex"><span style="width:180px">2018-04-05</span><span style="width:205px">2018-04-07</span><span style="width:160px">15</span><span>6%</span></div>
    <div style="display:flex"><span style="width:180px">2018-04-05</span><span style="width:205px">2018-04-07</span><span style="width:160px">16</span><span>9%</span></div>
    <div style="display:flex"><span style="width:180px">2018-04-05</span><span style="width:205px">2018-04-07</span><span style="width:160px">12</span><span>8%</span></div>
    <div style="display:flex"><span style="width:180px">2018-04-05</span><span style="width:205px">2018-04-07</span><span style="width:160px">19</span><span>6%</span></div>
  </div>
  <div class="abs" style="left:476px;top:730px;width:18px;height:360px;background:#4a4a4a;border-radius:9px"><div style="height:70px;background:#333;border-radius:9px"></div></div>
  <div class="abs" style="left:1237px;top:725px;width:18px;height:365px;background:#4a4a4a;border-radius:9px"><div style="height:75px;background:#333;border-radius:9px"></div></div>

  <!-- options panel -->
  <section class="abs modal">
    <div class="abs tab" style="left:235px;top:25px;width:155px;height:35px;background:var(--white)">Mode 1</div>
    <div class="abs tab" style="left:395px;top:15px;width:155px;height:45px;background:#1a1a1a;color:var(--white)">Mode 2</div>

    <div class="abs panel" style="left:15px;top:75px;width:370px;height:530px;overflow:hidden">
      <div class="abs field" style="left:16px;top:9px;width:181px;height:31px">Model name</div>
      <div class="abs btn" style="left:206px;top:9px;width:106px;height:30px;background:var(--teal);font-size:16px">Select</div>
      <div class="abs" style="left:0;top:50px;width:370px;border-top:1px solid #ececec"></div>
      <div class="abs" style="left:0;top:51px;width:330px;height:400px">
        <div class="model-item" style="top:0">Model 1</div>
        <div class="model-item" style="top:49px">Model 2</div>
        <div class="model-item selected" style="top:99px">Model 3</div>
        <div class="model-item" style="top:149px">Model 4</div>
        <div class="model-item" style="top:198px">Model 5</div>
        <div class="model-item" style="top:247px">Model 6</div>
        <div class="model-item" style="top:296px">Model 7</div>
        <div class="model-item" style="top:345px">Model 8</div>
      </div>
      <div class="abs" style="left:330px;top:51px;width:40px;height:399px;background:var(--scroll)">
        <div style="position:absolute;left:10px;top:24px;width:19px;height:350px;border:1px solid #999;border-radius:10px;background:#fff"><div style="height:75px;background:#999;border-radius:9px"></div></div>
      </div>
      <div class="abs" style="left:0;top:450px;width:370px;border-top:1px solid #ececec"></div>
      <div class="abs btn" style="left:87px;top:470px;width:195px;height:40px;background:var(--navy);font-size:14px;gap:12px">
        <svg width="22" height="22" viewBox="0 0 22 22"><circle cx="11" cy="11" r="9.5" fill="none" stroke="#fff" stroke-width="1.6"/><path d="M11 6v10M6 11h10" stroke="#fff" stroke-width="1.6"/></svg>ADD A MODEL</div>
    </div>

    <div class="abs panel" style="left:400px;top:75px;width:370px;height:530px;overflow:hidden">
      <div class="abs" style="left:0;top:0;width:370px;height:50px;background:var(--teal);color:var(--white);font-weight:700;font-size:18px;display:flex;align-items:center;justify-content:center">Parameters:</div>
      <div class="param" style="top:50px"><label>Entry:</label><div class="field">0.5</div></div>
      <div class="param" style="top:100px"><label>Exit:</label><div class="field">-0.3</div></div>
      <div class="param" style="top:150px"><label>Lookback:</label><div class="field">5</div></div>
      <div class="param" style="top:200px"><label>Entry:</label><div class="field">0.5</div></div>
      <div class="param" style="top:250px"><label>Exit:</label><div class="field">-0.3</div></div>
      <div class="param" style="top:300px"><label>Lookback:</label><div class="field">5</div></div>
      <div class="param" style="top:350px"><label>Entry:</label><div class="field">0.5</div></div>
      <div class="param" style="top:400px"><label>Exit:</label><div class="field">-0.3</div></div>
      <div class="abs btn" style="left:108px;top:465px;width:153px;height:48px;background:var(--navy);font-size:16px">RUN</div>
    </div>
  </section>

  <aside class="abs options">
    <div class="abs" style="left:8px;top:125px;transform:translate(-50%,-50%) rotate(-90deg);transform-origin:center;margin-left:13px;font-size:18px;font-weight:600;letter-spacing:1px;white-space:nowrap">OPTIONS</div>
    <svg class="abs" style="left:36px;top:111px" width="28" height="28" viewBox="0 0 28 28"><circle cx="14" cy="14" r="12.5" fill="var(--navy)" stroke="#fff" stroke-width="2"/><path d="M20 14H9m5-5-5 5 5 5" fill="none" stroke="#fff" stroke-width="2.2"/></svg>
  </aside>
</div>
</body>
</html>
```